Business card for Crestline Bathrooms

Please design a business card for our bathroom renovation business. You can use my existing logo, but if you have an idea to modernize it, I would like to see it. Please see attached files first. I would like to use the blue and the orange theme. I like the concept of using the shower head in the logo. Please find following a design (or two) that I have been trying to create with my limited resources. That design was for a sign, but I was going to adopt it and use it as a business card as well. I like the concept of the water splash but I don’t think it “flows” nicely together with the logo. Another thought is that maybe creating the logo out of water splash could work and have a dramatic effect (like the water text and the butterfly picture attached with similar background instead of white). If the above doesn’t work I would like to see a modern simplified design. One of the attached files named as the unwanted business card has all the details that I want included in the business card. Please note that it is two sided.
Updates

I am very thankful for the designs that I have received, but they are very similar and only a couple of attempts to do something with the water splash as per my original brief. Modernizing the logo and having it made out of out of water splash with the orange as color accent could work and have a dramatic effect (like the water text and the butterfly picture attached with similar background instead of white). Please do not use the butterfly itself! This is just an example that images can be created out of water splash.

Contact Information for Business Card

all the details are on the unwonted business card file included

Colors
3176b5

Requirements
Nice to have
• Copied from the brief:
• ... maybe creating the logo out of water splash could work and have a dramatic effect (like the water text and the butterfly picture attached with similar background instead of white). Please do not use the butterfly itself!
Should not have
• I am getting designs with a butterfly. The butterfly picture was an example of creating something from a water splash. The butterfly itself has no association with anything other than the concept of creating a logo out of water splash. Sorry, I thought I was clear in the brief.

```html
<!DOCTYPE html>
<html lang="en">
<head>
<meta charset="utf-8">
<title>Crestline Bathrooms – Business Card</title>
<link href="https://fonts.googleapis.com/css2?family=Roboto:wght@400;500;700&family=Patrick+Hand&display=swap" rel="stylesheet">
<style>
  :root {
    --backdrop: #e4e4e4;
    --navy: #1a2f50;
    --white: #ffffff;
    --coral: #ee7a66;
    --splash-light: rgba(196, 218, 235, 0.62);
    --splash-mid: rgba(120, 160, 195, 0.35);
  }
  * { margin: 0; padding: 0; box-sizing: border-box; }
  html, body { width: 1200px; height: 960px; overflow: hidden; }
  body {
    background: var(--backdrop);
    font-family: "Roboto", Arial, sans-serif;
    position: relative;
  }
  .card {
    position: absolute;
    width: 600px;
    height: 343px;
    background: var(--navy);
    overflow: hidden;
    color: var(--white);
  }
  .card--services { left: 302px; top: 124px; }
  .card--contact { left: 299px; top: 493px; }

  .splash {
    position: absolute;
    top: 0;
    height: 100%;
  }
  .card--services .splash {
    left: 0; width: 230px;
    background:
      radial-gradient(ellipse 55% 38% at 45% 78%, var(--splash-light), transparent 75%),
      radial-gradient(ellipse 30% 60% at 62% 30%, var(--splash-mid), transparent 75%),
      radial-gradient(ellipse 35% 40% at 18% 20%, var(--splash-mid), transparent 75%);
  }
  .card--contact .splash {
    left: 340px; width: 260px;
    background:
      radial-gradient(ellipse 50% 40% at 50% 75%, var(--splash-light), transparent 75%),
      radial-gradient(ellipse 28% 60% at 30% 30%, var(--splash-mid), transparent 75%),
      radial-gradient(ellipse 35% 40% at 82% 22%, var(--splash-mid), transparent 75%);
  }

  .services {
    position: absolute;
    right: 42px;
    top: 60px;
    list-style: none;
    text-align: right;
  }
  .services li {
    font-size: 15px;
    line-height: 24px;
    letter-spacing: 0.1px;
  }
  .services li::after {
    content: "";
    display: inline-block;
    width: 6px; height: 6px;
    border-radius: 50%;
    background: var(--coral);
    margin-left: 8px;
    vertical-align: middle;
  }

  .memberships {
    position: absolute;
    right: 44px;
    top: 262px;
    display: flex;
    align-items: center;
    gap: 28px;
  }
  .badge { background: var(--white); }
  .badge--square { width: 32px; height: 32px; border-radius: 6px; }
  .badge--wide { width: 118px; height: 26px; border-radius: 3px; }

  .brand {
    position: absolute;
    left: 112px;
    top: 48px;
    width: 200px;
    text-align: center;
  }
  .brand-mark {
    display: block;
    width: 18px; height: 18px;
    border-radius: 50%;
    background: var(--coral);
    margin: 0 auto 8px;
  }
  .brand-name {
    font-size: 30px;
    font-weight: 500;
    line-height: 34px;
    color: var(--white);
  }

  .contact {
    position: absolute;
    left: 31px;
    top: 172px;
  }
  .contact-name {
    font-family: "Patrick Hand", cursive;
    font-size: 25px;
    color: var(--coral);
    line-height: 30px;
    margin-bottom: 4px;
  }
  .contact-line {
    display: flex;
    align-items: center;
    font-size: 17px;
    line-height: 21.5px;
  }
  .contact-line--phone { font-size: 18px; font-weight: 700; line-height: 24px; }
  .contact-line .sep { margin: 0 14px; font-weight: 400; }
  .icon {
    width: 14px; height: 14px;
    margin-right: 8px;
    flex-shrink: 0;
    fill: var(--coral);
  }
  .abn {
    font-size: 10px;
    margin: 12px 0 0 19px;
  }
</style>
</head>
<body>

  <section class="card card--services">
    <div class="splash" role="img" aria-label="Photograph of a clear water splash arcing across the card"></div>
    <ul class="services">
      <li>Complete Bathroom Renovations &amp; Remodelling</li>
      <li>Professional Service From Concept To Completion</li>
      <li>Highly Skilled &amp; Qualified Tradespeople</li>
      <li>All Work Guaranteed</li>
    </ul>
    <div class="memberships">
      <span class="badge badge--square" aria-label="Industry association membership"></span>
      <span class="badge badge--wide" aria-label="Builders association membership"></span>
    </div>
  </section>

  <section class="card card--contact">
    <div class="splash" role="img" aria-label="Photograph of a clear water splash rising up the right edge"></div>

    <div class="brand">
      <span class="brand-mark"></span>
      <div class="brand-name">Crestline<br>Bathrooms</div>
    </div>

    <div class="contact">
      <div class="contact-name">Daniel Marsh</div>
      <div class="contact-line contact-line--phone">
        <svg class="icon" viewBox="0 0 16 16"><path d="M3.6 1.2l2.3 2.6c.3.4.3.9 0 1.3L4.8 6.3c.8 1.9 2.9 4 4.9 4.9l1.2-1.1c.4-.3.9-.3 1.3 0l2.6 2.3c.4.4.4 1 0 1.4l-1.3 1.3C11.2 17 .9 6.7 2 4.4l.3-.5 1.3-1.3z" transform="translate(0 -1)"/></svg>
        0400 123 456<span class="sep">|</span>6200 4417
      </div>
      <div class="contact-line">
        <svg class="icon" viewBox="0 0 16 16"><path d="M8 1a7 7 0 1 0 3.6 13l-.6-1.2A5.7 5.7 0 1 1 13.7 8c0 1.3-.6 2-1.3 2s-1-.5-1-1.3V4.5h-1.3v.6A3.2 3.2 0 1 0 10.4 11c.4.7 1.1 1.2 2 1.2 1.6 0 2.6-1.5 2.6-3.9A7 7 0 0 0 8 1zm0 9.1a2 2 0 1 1 0-4.1 2 2 0 0 1 0 4.1z"/></svg>
        daniel@crestlinebathrooms.com.au
      </div>
      <div class="contact-line">
        <svg class="icon" viewBox="0 0 16 16"><path d="M8 1a7 7 0 1 0 0 14A7 7 0 0 0 8 1zm0 1.5c.9 0 1.9 1.6 2.2 4H5.8C6.1 4.1 7.1 2.5 8 2.5zM2.6 9.5h2.1c.1 1.5.5 2.9 1 3.8a5.6 5.6 0 0 1-3.1-3.8zm0-3a5.6 5.6 0 0 1 3.1-3.8c-.5.9-.9 2.3-1 3.8zM8 13.5c-.9 0-1.9-1.6-2.2-4h4.4c-.3 2.4-1.3 4-2.2 4zm2.3-.2c.5-.9.9-2.3 1-3.8h2.1a5.6 5.6 0 0 1-3.1 3.8zm1-6.8c-.1-1.5-.5-2.9-1-3.8a5.6 5.6 0 0 1 3.1 3.8z"/></svg>
        crestlinebathrooms.com.au
      </div>
      <div class="contact-line">
        <svg class="icon" viewBox="0 0 16 16"><path d="M1 4h14v1.2L8 9.4 1 5.2zm0 2.6l7 4.2 7-4.2V13H1z"/></svg>
        PO Box 41 Riverton 2600
      </div>
      <div class="abn">ABN 12 345 678 901</div>
    </div>
  </section>

</body>
</html>
```